Infographic for a Christian church discipleship pathway

We need to take a fairly complex program that helps people in a Baptist church follow Jesus, and turn it into a simple graphic. This graphic does not have to explain the whole program, web pages and print materials will do that. But, it should be something that people see and understand what it is quickly. The attached graphic is only to give the key words and general direction of the program. It should not serve as a design guide. In other words, we want to see some other ideas how this information can be imparted graphically with concision and creativity. It's important to note, the categories at the top (pray daily, read daily, gather weekly) are first steps, starting points....one shouldn't move forward until they've incorporated these things into their life. However, the categories that follow (study, connect, serve, etc) are not necessarily steps to take in sequential order.

The diagrams we've provided are not what we expect. They are only to explain the program. Here is a verbal description: The motto of our church is "A Ready Church" (ready to serve, ready to love, ready for when Jesus returns). There are four words that describe a ready church member: FOCUSED on the return of Christ, FAITHFUL in a daily relationship with Jesus, PREPARED for any opportunity to be a supernatural vessel of God's worK, LOOKING to invite others into God's family. The first two are God's Work in Me (Focused and faithful); the second two are God's Work Through me (Prepared, looking). Please use those two things as you wish (Focused faithful prepared looking; and God's word in and through me). If they are clarifying, please use. If not, you don't have to use.

Additionally, the strategies we employ to be "a ready church" are 1. Prayer 2. God's Word, and 3. Biblical Community. (So, in other words, these three things help us be a people who is focused, faithful, prepared, and looking....which is a ready church.

To provide some information how we will build this out: this graphic will be used in print and digital content. The digital content will allow people to click on each category to access training and resources associated with that discipline. (Fasting, reflecting, etc).

www.kvt.church

Target Market(s)

35-50

Industry/Entity Type

Religious

Other font styles liked:
• Lato and/or Cambria

Requirements
Must have
• Fonts: lato, cambria. Colors#: 373E41, ebebe8, #a69677. Accent Colors: 80401D, #4e5730, #a5bac8
Nice to have
• A designer who has an understanding of what it means to incorporate the spiritual disciplines of the Christian faith into their life.

```html
<!DOCTYPE html>
<html lang="en">
<head>
<meta charset="utf-8">
<title>A Ready Church – Discipleship Pathway</title>
<link rel="stylesheet" href="https://fonts.googleapis.com/css2?family=Outfit:wght@300;400;500;600;700;800&display=swap">
<style>
  :root {
    --ink: #373e41;
    --ink-soft: #2f3538;
    --paper: #ffffff;
    --olive: #5d6640;
    --olive-band: #6a7150;
    --slate: #96a4b4;
    --slate-text: #8e9aab;
    --sage: #a9b8b8;
    --sage-text: #a3b3b3;
    --prayer-bg: #d6e2ee;
    --prayer-cell: #cddbe8;
    --word-bg: #e3e3dd;
    --word-cell: #d8d8d1;
    --community-bg: #dee3e3;
    --community-cell: #d2d9d9;
    --pill-line: #8a96a2;
  }
  * { box-sizing: border-box; margin: 0; padding: 0; }
  html, body { width: 1200px; height: 816px; overflow: hidden; background: var(--paper); }
  body { font-family: "Outfit", sans-serif; color: var(--ink); }
  .canvas { position: relative; width: 1200px; height: 816px; background: var(--paper); }

  /* Left sidebar */
  .sidebar { position: absolute; left: 0; top: 0; width: 338px; height: 816px;
    background: linear-gradient(180deg, #353c3f 0%, #434a4d 30%, #4b5154 55%, #2f3538 100%); }
  .church-name { position: absolute; left: 79px; top: 70px; display: flex; align-items: center; gap: 12px; color: #fff; }
  .church-name .mark { width: 46px; height: 60px; border: 2px solid #fff; }
  .church-name span { font-weight: 600; font-size: 19px; line-height: 1.12; letter-spacing: .5px; text-transform: uppercase; }
  .start-here { position: absolute; left: 126px; top: 316px; color: #fff; font-weight: 500; font-size: 23px; letter-spacing: 5px; }

  .start-arrow { position: absolute; left: 353px; top: 318px; }

  .pill { position: absolute; left: 69px; width: 327px; height: 98px; background: #fff;
    border: 1.5px solid var(--pill-line); border-radius: 49px; text-align: center;
    display: flex; flex-direction: column; justify-content: center; }
  .pill h3 { font-weight: 700; font-size: 22px; letter-spacing: -.3px; color: var(--ink); }
  .pill p { font-weight: 300; font-size: 14px; margin-top: 2px; }
  .pill.in-me { top: 391px; }
  .pill.through-me { top: 601px; }

  /* Title */
  .title { position: absolute; left: 430px; top: 66px; width: 690px; text-align: center;
    font-weight: 800; font-size: 76px; line-height: 1; letter-spacing: -1px; color: var(--ink); }
  .motto { position: absolute; left: 432px; top: 135px; width: 686px; text-align: center;
    font-weight: 600; font-size: 13.5px; letter-spacing: 2.2px; color: var(--olive); }

  /* Strategies */
  .strategy { position: absolute; top: 192px; width: 223px; text-align: center; }
  .strategy h4 { font-weight: 600; font-size: 17px; }
  .strategy p { font-weight: 400; font-size: 10.5px; line-height: 1.35; margin-top: 4px; color: var(--ink); }
  .strategy.prayer { left: 415px; } .strategy.prayer h4 { color: var(--slate-text); }
  .strategy.word { left: 665px; } .strategy.word h4 { color: var(--olive); }
  .strategy.community { left: 888px; width: 250px; } .strategy.community h4 { color: var(--sage-text); }

  /* Columns */
  .column { position: absolute; top: 298px; width: 223px; height: 447px; border-radius: 18px; }
  .column.prayer { left: 426px; background: var(--prayer-bg); --band: var(--slate); --cell: var(--prayer-cell); }
  .column.word { left: 665px; background: var(--word-bg); --band: var(--olive-band); --cell: var(--word-cell); }
  .column.community { left: 903px; background: var(--community-bg); --band: var(--sage); --cell: var(--community-cell); }

  .band { position: relative; height: 50px; background: var(--band); border-radius: 18px 18px 0 0;
    color: #fff; font-weight: 600; font-size: 16px; text-align: center; padding-top: 28px; line-height: 1; }
  .band .notch { position: absolute; right: -10px; top: 25px; width: 0; height: 0;
    border-top: 8px solid transparent; border-bottom: 8px solid transparent; border-left: 10px solid var(--band); }
  .badge { position: absolute; left: 50%; top: -30px; transform: translateX(-50%); width: 44px; height: 44px;
    border-radius: 50%; background: #fff; border: 3px solid var(--band); box-shadow: 0 0 0 5px rgba(255,255,255,.6);
    display: flex; align-items: center; justify-content: center; font-weight: 700; font-size: 26px; color: var(--ink); }

  .steps { list-style: none; }
  .steps li { position: absolute; left: 9px; right: 9px; height: 90px; border-radius: 6px;
    background: linear-gradient(180deg, rgba(255,255,255,.18), var(--cell));
    box-shadow: 0 2px 3px rgba(0,0,0,.06);
    display: flex; align-items: center; justify-content: center; font-size: 15px; font-weight: 400; color: var(--ink-soft); }
  .steps li:nth-child(1) { top: 52px; height: 80px; }
  .steps li:nth-child(2) { top: 138px; }
  .steps li:nth-child(3) { top: 241px; }
  .steps li:nth-child(4) { top: 345px; }

  .link-arrow { position: absolute; }
</style>
</head>
<body>
<svg width="0" height="0" style="position:absolute">
  <defs>
    <symbol id="arrow" viewBox="0 0 30 18">
      <rect x="0" y="5" width="2" height="8" fill="#373e41"/>
      <rect x="4" y="5" width="2" height="8" fill="#373e41"/>
      <rect x="8" y="5" width="10" height="8" fill="#373e41"/>
      <polygon points="17,0 30,9 17,18" fill="#373e41"/>
    </symbol>
  </defs>
</svg>

<main class="canvas">
  <aside class="sidebar" role="img" aria-label="Muted photograph of a church sanctuary interior with a rose window and altar">
  </aside>
  <div class="church-name"><div class="mark"></div><span>Kent Valley<br>Tabernacle</span></div>
  <div class="start-here">START HERE</div>
  <svg class="start-arrow" width="45" height="24"><use href="#arrow"/></svg>

  <div class="pill in-me"><h3>Focused. Faithful</h3><p>God’s Work in me</p></div>
  <div class="pill through-me"><h3>Prepared. Looking</h3><p>God’s Work thorough me</p></div>

  <h1 class="title">A READY CHURCH</h1>
  <p class="motto">READY TO SERVE, READY TO LOVE, READY FOR WHEN JESUS RETURNS</p>

  <div class="strategy prayer"><h4>PRAYER</h4><p>Become a person devoted to<br>prayer each day of your life</p></div>
  <div class="strategy word"><h4>GOD’S WORD</h4><p>Build a daily habit of<br>beholding God in his Word</p></div>
  <div class="strategy community"><h4>BIBLICAL COMMUNITY</h4><p>Engage deeply in christian<br>community</p></div>

  <section class="column prayer">
    <div class="band"><span class="badge">P</span>PRAY DAILY<span class="notch"></span></div>
    <ul class="steps"><li>REST</li><li>REFLECT</li><li>FAST</li><li>INTERCEDE</li></ul>
  </section>
  <section class="column word">
    <div class="band"><span class="badge">G</span>GOD’S WORD<span class="notch"></span></div>
    <ul class="steps"><li>STUDY</li><li>MEMORIZE</li><li>TEACH</li><li>PROCLAIM</li></ul>
  </section>
  <section class="column community">
    <div class="band"><span class="badge">B</span>BIBLICAL COMMUNITY</div>
    <ul class="steps"><li>CONNECT</li><li>LEARN</li><li>GIVE</li><li>SERVE</li></ul>
  </section>

  <svg class="link-arrow" style="left:651px;top:383px" width="27" height="14"><use href="#arrow"/></svg>
  <svg class="link-arrow" style="left:651px;top:474px" width="27" height="14"><use href="#arrow"/></svg>
  <svg class="link-arrow" style="left:651px;top:577px" width="27" height="14"><use href="#arrow"/></svg>
  <svg class="link-arrow" style="left:651px;top:681px" width="27" height="14"><use href="#arrow"/></svg>
  <svg class="link-arrow" style="left:889px;top:383px" width="27" height="14"><use href="#arrow"/></svg>
  <svg class="link-arrow" style="left:889px;top:474px" width="27" height="14"><use href="#arrow"/></svg>
  <svg class="link-arrow" style="left:889px;top:577px" width="27" height="14"><use href="#arrow"/></svg>
  <svg class="link-arrow" style="left:889px;top:681px" width="27" height="14"><use href="#arrow"/></svg>
</main>
</body>
</html>
```